Debut book club fiction author needs a book cover design

I need a book cover design (and a separate e-book thumbnail also) for my book club/women's fiction debut that I am launching on Pagewell Indie Press. I've included the brief/back cover blurb as below to give you a flavour of the book. I'm after something striking but simple, maybe with a wine glass lurking in the background and/or an abandoned dummy/pacifier or empty crib?? I've attached a few competitor style covers that i like for reference.

Target Market(s)

Women's fiction readers

Industry/Entity Type

Women's fiction/publishing

Font styles to use
Serif

Requirements
Must have
• Title: Beneath the Quiet Hours. Name: Linda Harwick. The full 'pitch/blurb' on the back cover which I've included as a file below named 'pitch'
Nice to have
• Open to suggestions, but an image which reflects the struggle captured in the book in a bold simple image

```html
<!DOCTYPE html>
<html lang="en">
<head>
<meta charset="utf-8">
<title>Beneath the Quiet Hours — Linda Harwick</title>
<link rel="stylesheet" href="https://fonts.googleapis.com/css2?family=Oranienbaum&family=Libre+Bodoni:wght@700&display=swap">
<style>
  :root {
    --stage: #626262;
    --cover-black: #0b0b0b;
    --title-white: #ffffff;
    --title-magenta: #cc0a78;
    --shadow-ink: #000000;
    --wood-light: #9a7a55;
    --wood-mid: #4f3827;
    --napkin: #6e3a20;
    --wine: #5a1414;
    --pacifier: #e0369a;
    --pacifier-core: #f2e6ee;
  }
  * { margin: 0; padding: 0; box-sizing: border-box; }
  html, body {
    width: 1200px;
    height: 784px;
    overflow: hidden;
    background: var(--stage);
  }
  .canvas {
    position: relative;
    width: 1200px;
    height: 784px;
  }
  .book-cover {
    position: absolute;
    left: 355px;
    top: 33px;
    width: 490px;
    height: 718px;
    background: var(--cover-black);
    overflow: hidden;
  }
  .cover-scene {
    position: absolute;
    inset: 0;
    width: 100%;
    height: 100%;
  }
  .title {
    font-weight: normal;
  }
  .title-line {
    position: absolute;
    left: 32px;
    display: block;
    font-family: "Oranienbaum", "Bodoni Moda", serif;
    line-height: 1;
    white-space: nowrap;
    text-shadow: 4px 4px 0 var(--shadow-ink);
  }
  .title-lead {
    top: 92px;
    font-size: 84px;
    letter-spacing: -1px;
    color: var(--title-white);
  }
  .title-quiet {
    top: 169px;
    font-size: 128px;
    letter-spacing: -2px;
    color: var(--title-magenta);
  }
  .title-hours {
    top: 274px;
    font-size: 156px;
    letter-spacing: -3px;
    color: var(--title-magenta);
  }
  .author {
    position: absolute;
    left: 0;
    right: 0;
    top: 671px;
    text-align: center;
    font-family: "Libre Bodoni", "Times New Roman", serif;
    font-weight: 700;
    font-size: 36px;
    line-height: 1;
    letter-spacing: 1px;
    color: var(--title-white);
  }
</style>
</head>
<body>
<main class="canvas">
  <section class="book-cover">
    <svg class="cover-scene" viewBox="0 0 490 718" role="img"
         aria-label="Dimly lit wooden table with an abandoned pink pacifier in a pool of light, a folded napkin and a wine glass lurking in the shadows">
      <defs>
        <radialGradient id="back-glow" cx="0.5" cy="0.62" r="0.55">
          <stop offset="0" stop-color="#2c221b"/>
          <stop offset="1" stop-color="#0b0b0b" stop-opacity="0"/>
        </radialGradient>
        <radialGradient id="table-light">
          <stop offset="0" stop-color="var(--wood-light)"/>
          <stop offset="0.5" stop-color="var(--wood-mid)"/>
          <stop offset="1" stop-color="#0b0b0b" stop-opacity="0"/>
        </radialGradient>
        <radialGradient id="napkin-tone">
          <stop offset="0" stop-color="var(--napkin)"/>
          <stop offset="1" stop-color="var(--napkin)" stop-opacity="0"/>
        </radialGradient>
        <linearGradient id="wine-tone" x1="0" y1="0" x2="0" y2="1">
          <stop offset="0" stop-color="#2a2a2a" stop-opacity="0"/>
          <stop offset="0.45" stop-color="var(--wine)" stop-opacity="0.7"/>
          <stop offset="1" stop-color="#2a2a2a" stop-opacity="0"/>
        </linearGradient>
        <radialGradient id="pacifier-tone">
          <stop offset="0" stop-color="var(--pacifier-core)"/>
          <stop offset="0.25" stop-color="var(--pacifier)"/>
          <stop offset="0.8" stop-color="var(--title-magenta)" stop-opacity="0.6"/>
          <stop offset="1" stop-color="var(--title-magenta)" stop-opacity="0"/>
        </radialGradient>
      </defs>
      <rect width="490" height="718" fill="url(#back-glow)"/>
      <ellipse cx="240" cy="555" rx="250" ry="75" fill="url(#table-light)"/>
      <ellipse cx="375" cy="300" rx="32" ry="120" fill="url(#wine-tone)"/>
      <ellipse cx="395" cy="505" rx="90" ry="55" fill="url(#napkin-tone)"/>
      <ellipse cx="234" cy="555" rx="66" ry="62" fill="url(#pacifier-tone)"/>
    </svg>
    <h1 class="title">
      <span class="title-line title-lead">BENEATH THE</span>
      <span class="title-line title-quiet">QUIET</span>
      <span class="title-line title-hours">HOURS</span>
    </h1>
    <p class="author">LINDA HARWICK</p>
  </section>
</main>
</body>
</html>
```